​Silver Harbor Rhythm provides personal, friendly service in a fun and high energy environment. We are based in Vermont.

We would like a card that appeals to a wide range of audiences as we do a wide range of events. Please feel free to check out our website silverharborrhythm.net for inspiration.

Target Market(s)

weddings, corporate, birthday parties, colleges

Industry/Entity Type

Business

Contact Information for Business Card

Silver Harbor Rhythm
Providing Entertainment For All Occasions
555 274 9160
silverharborrhythm@mailnest.net
silverharborrhythm.net

```html
<!DOCTYPE html>
<html lang="en">
<head>
<meta charset="utf-8">
<title>Silver Harbor Rhythm – Business Card</title>
<link href="https://fonts.googleapis.com/css2?family=Open+Sans:wght@400;600;700&display=swap" rel="stylesheet">
<style>
  :root {
    --page-bg: #ecebe8;
    --card-front: #ffffff;
    --card-back: #0c0c0c;
    --brand-green: #2f6b2a;
    --text-dark: #333333;
    --rule-grey: #c9c9c9;
    --icon-grey: #4a4a4a;
    --back-text: #f2f2f2;
  }
  * { margin: 0; padding: 0; box-sizing: border-box; }
  html, body { width: 1200px; height: 1200px; overflow: hidden; }
  body {
    background: var(--page-bg);
    font-family: "Open Sans", Arial, sans-serif;
    display: flex;
    flex-direction: column;
    align-items: center;
    justify-content: center;
    gap: 60px;
  }
  .card {
    width: 900px;
    height: 515px;
    border-radius: 34px;
    position: relative;
    box-shadow: 0 6px 22px rgba(0,0,0,0.12);
  }
  .card-front {
    background: var(--card-front);
    display: flex;
    flex-direction: column;
    align-items: center;
    padding-top: 120px;
  }
  .brand-name {
    font-weight: 700;
    font-size: 52px;
    letter-spacing: 1px;
    color: var(--brand-green);
    text-transform: uppercase;
    display: flex;
    align-items: center;
    gap: 18px;
  }
  .brand-mark {
    width: 22px; height: 22px;
    border-radius: 50%;
    background: var(--brand-green);
  }
  .holder-name {
    margin-top: 54px;
    font-weight: 700;
    font-size: 32px;
    color: var(--brand-green);
  }
  .divider {
    width: 680px;
    height: 2px;
    background: var(--rule-grey);
    margin-top: 14px;
  }
  .address {
    margin-top: 30px;
    font-size: 22px;
    color: var(--text-dark);
  }
  .contact-row {
    margin-top: 12px;
    display: flex;
    gap: 34px;
    font-size: 22px;
    color: var(--text-dark);
  }
  .contact-item { display: flex; align-items: center; gap: 8px; }
  .contact-item svg { width: 20px; height: 20px; fill: var(--icon-grey); }
  .card-back {
    background: var(--card-back);
    display: flex;
    flex-direction: column;
    align-items: center;
    justify-content: center;
  }
  .back-brand {
    font-weight: 700;
    font-size: 64px;
    letter-spacing: 2px;
    color: var(--back-text);
    text-transform: uppercase;
    margin-top: -40px;
  }
  .back-url {
    margin-top: 110px;
    font-size: 30px;
    font-weight: 600;
    letter-spacing: 2px;
    color: var(--back-text);
  }
</style>
</head>
<body>
  <section class="card card-front">
    <div class="brand-name"><span class="brand-mark"></span>Silver Harbor Rhythm</div>
    <div class="holder-name">Your Name, Title</div>
    <div class="divider"></div>
    <div class="address">Sreet Name, City Name, Zip Code-00000</div>
    <div class="contact-row">
      <span class="contact-item">
        <svg viewBox="0 0 20 20" aria-hidden="true"><circle cx="10" cy="10" r="10"/><path d="M6.5 5.5l2 2-1 1.2c.7 1.5 1.8 2.6 3.3 3.3l1.2-1 2 2-1.3 1.5c-3.6-.6-6.7-3.7-7.3-7.3z" fill="#fff"/></svg>
        555 274 9160
      </span>
    </div>
    <div class="contact-row">
      <span class="contact-item">
        <svg viewBox="0 0 20 20" aria-hidden="true"><circle cx="10" cy="10" r="10"/><rect x="5" y="6.5" width="10" height="7" fill="#fff"/><path d="M5 6.5l5 4 5-4" stroke="#4a4a4a" stroke-width="1" fill="none"/></svg>
        silverharborrhythm@mailnest.net
      </span>
      <span class="contact-item">
        <svg viewBox="0 0 20 20" aria-hidden="true"><circle cx="10" cy="10" r="10"/><circle cx="10" cy="10" r="5.5" fill="none" stroke="#fff" stroke-width="1.2"/><path d="M4.5 10h11M10 4.5c-2.5 3-2.5 8 0 11M10 4.5c2.5 3 2.5 8 0 11" fill="none" stroke="#fff" stroke-width="1"/></svg>
        www.silverharborrhythm.net
      </span>
    </div>
  </section>

  <section class="card card-back">
    <div class="back-brand">Silver Harbor Rhythm</div>
    <div class="back-url">www.silverharborrhythm.net</div>
  </section>
</body>
</html>
```